Business Cards Design for the electrical wholesaler: clean bold dynamic :)

We need a business card design that would follow our latest brand guidelines. As an electrical wholesaler we want to bring a fresh look and feel into the industry. The design should be clean bold and dynamic. It should come alive with the renewed energy of our green colour. Our grey colour should keep things balanced and complement the notion of maturity and responsibility. We employ Lato as a corporate font however are not bound by this font and we’re open to interpretation here.

Target Market(s)

Electrical contractors

Industry/Entity Type

Business

Contact Information for Business Card

Logo
Name & Surname: Halyna Dorosh
Job Title: Director of Marketing
Email: halya.dorosh@quillmail.example
Cell phone: XXX.XXX.XXXX
Address: 20517 - 87 Ave. Edmonton, AB, Canada. T6K 4N8
Business Phone: 780.555.0184
Website: www.brovix.example

Font styles to use
Other font styles liked:
• Lato

Requirements
Must have
• Logo & website
Nice to have
• Brand elements - some of them you may find in the attached Brand Guidelines (e.g. three lines on the background signifying "W")

```html
<!DOCTYPE html>
<html lang="en">
<head>
<meta charset="utf-8">
<title>Brovix business card</title>
<link href="https://fonts.googleapis.com/css2?family=Lato:wght@400;700&display=swap" rel="stylesheet">
<style>
  :root {
    --green: #8bbf3f;
    --grey: #4d4d4f;
    --text: #4a4a4a;
    --rule: #8a8a8a;
    --paper: #f7f7f5;
    --backdrop: #2b2b2b;
  }
  * { margin: 0; padding: 0; box-sizing: border-box; }
  html, body { width: 1200px; height: 960px; overflow: hidden; }
  body { background: var(--backdrop); font-family: "Lato", sans-serif; position: relative; }

  .card { position: absolute; width: 600px; height: 342px; border-radius: 18px; overflow: hidden; }
  .card-front { left: 314px; top: 113px; background: var(--paper); }
  .card-back { left: 311px; top: 472px; background: var(--green); }

  .brand { position: absolute; right: 36px; top: 48px; display: flex; align-items: center; gap: 10px; }
  .brand-mark { width: 22px; height: 22px; background: var(--green); }
  .brand-name { font-size: 44px; font-weight: 700; color: var(--grey); line-height: 1; }

  .name-tab { position: absolute; left: 0; top: 154px; width: 14px; height: 36px; background: var(--green); }
  .person-name { position: absolute; left: 36px; top: 151px; font-size: 20px; font-weight: 700; color: var(--green); text-transform: uppercase; }
  .person-title { position: absolute; left: 36px; top: 175px; font-size: 15px; color: var(--text); text-transform: uppercase; }
  .divider { position: absolute; left: 40px; right: 35px; top: 203px; height: 1px; background: var(--rule); }

  .contacts { position: absolute; left: 37px; top: 216px; list-style: none; }
  .contacts li { display: flex; align-items: center; height: 19px; font-size: 14px; color: var(--text); }
  .contacts svg { width: 14px; height: 14px; margin-right: 8px; fill: var(--green); }

  .address { position: absolute; right: 35px; top: 255px; text-align: right; font-size: 14px; line-height: 19px; color: var(--text); }

  .footer-bands { position: absolute; left: 0; bottom: 0; width: 600px; height: 342px; }
  .footer-url { position: absolute; right: 34px; top: 313px; font-size: 14px; color: #fff; }

  .back-name { position: absolute; left: 0; right: 0; top: 108px; text-align: center; font-size: 92px; font-weight: 700; color: #fff; line-height: 1; }
  .back-url { position: absolute; left: 0; right: 0; top: 292px; text-align: center; font-size: 13px; letter-spacing: 3.2px; color: #fff; }
</style>
</head>
<body>

<section class="card card-front">
  <div class="brand">
    <span class="brand-mark"></span>
    <span class="brand-name">brovix</span>
  </div>

  <div class="name-tab"></div>
  <h1 class="person-name">Halyna Dorosh</h1>
  <p class="person-title">CEO/Founder</p>
  <div class="divider"></div>

  <ul class="contacts">
    <li>
      <svg viewBox="0 0 16 16" aria-hidden="true"><path d="M3.5 1l2.5 3-1.5 2c1 2 2.5 3.5 4.5 4.5l2-1.5 3 2.5-1.5 2.5C7 14 2 9 1 2.5z"/></svg>
      780.555.0184
    </li>
    <li>
      <svg viewBox="0 0 16 16" aria-hidden="true"><path d="M4 0h8a1 1 0 0 1 1 1v14a1 1 0 0 1-1 1H4a1 1 0 0 1-1-1V1a1 1 0 0 1 1-1zm1 2v10h6V2zm3 11a1 1 0 1 0 0 2 1 1 0 0 0 0-2z"/></svg>
      780.555.0127
    </li>
    <li>
      <svg viewBox="0 0 16 16" aria-hidden="true"><path d="M4 1h8v4H4zM1 6h14v6h-3v3H4v-3H1zm4 4v4h6v-4z"/></svg>
      780.555.0193
    </li>
    <li>
      <svg viewBox="0 0 16 16" aria-hidden="true"><path d="M1 3h14v1.5L8 9 1 4.5zm0 3l7 4.5L15 6v7H1z"/></svg>
      halya.dorosh@quillmail.example
    </li>
  </ul>

  <address class="address" style="font-style:normal">
    20517 - 87 Ave.<br>
    Edmonton, AB, Canada. T6K 4N8
  </address>

  <svg class="footer-bands" viewBox="0 0 600 342" aria-hidden="true">
    <path d="M0 320H352L345 332H0Z" fill="var(--grey)"/>
    <path d="M0 337H342L364 302H600V342H0Z" fill="var(--green)"/>
  </svg>
  <span class="footer-url">www.brovix.example</span>
</section>

<section class="card card-back">
  <p class="back-name">brovix</p>
  <p class="back-url">www.brovix.example</p>
</section>

</body>
</html>
```